Logo and Card design for KRV Home Solutions LLC

I need an edgier logo and business card designs. Current logo attached. I like the colors below. I would like the logo to incorporate a home in the design.
Title = Principal-Acquisitions
Email:KRVHOMESOLUTIONS@fernmail.example
555-214-0937
facebook
IG
2 sided business card with the front being contact info a slogan about selling a home fast. The back incorporating What we do. Buy houses, land, or commercial property as is. We find solutions to make the process of selling simple and fair.

Target Market(s)

Motivated house sellers.

Industry/Entity Type

Business

Contact Information for Business Card

Who we are: We are a Faith based Real Estate Investment Company. We pay cash for homes in any condition and can close quick. Whatever the reason you need to sell fast, we can help. We believe in creating win-win solutions to help you in your time of need. We care! We can help!

Logo Text

KRV Home Solutions LLC

Font styles to use
Sans Serif

Colors
33a6d7
0355a3
85abd2
cee9f5
9d9d9d
b2b2b2
ffffff

Requirements
Must have
• Old logo attached. I want something edgier.
• Company name, phone number, description on the back of what we can do. Pay all cash. Buy in as is condition. No fees,Commisions or closing costs.Close quick. No hassles with solutions to meet your unique situation.
• Call today for an offer within 24 hours.

```html
<!DOCTYPE html>
<html lang="en">
<head>
<meta charset="UTF-8">
<title>KRV Home Solutions – Business Card</title>
<link rel="stylesheet" href="https://fonts.googleapis.com/css2?family=Montserrat:wght@600&family=Work+Sans:wght@400;500&display=swap">
<style>
  :root {
    --navy: #22386f;
    --rule: #2f4a8a;
    --slate: #555555;
    --ink: #3a3a3a;
    --paper: #ffffff;
    --backdrop: #2b2b2b;
  }
  * { margin: 0; padding: 0; box-sizing: border-box; }
  html, body { width: 1200px; height: 900px; overflow: hidden; background: var(--backdrop); }
  .canvas {
    width: 1200px; height: 900px;
    display: flex; flex-direction: column; align-items: center; justify-content: center; gap: 40px;
  }
  .card {
    width: 700px; height: 400px; position: relative;
    font-family: "Work Sans", sans-serif;
  }
  .card--back { background: var(--navy); color: var(--paper); }
  .card--front { background: var(--paper); color: var(--ink); }

  .brand {
    position: absolute; left: 50%; transform: translateX(-50%);
    display: flex; align-items: center; gap: 16px;
  }
  .brand__mark { width: 22px; height: 22px; }
  .brand__name {
    font-family: "Montserrat", sans-serif; font-weight: 600;
    font-size: 40px; letter-spacing: 2px; line-height: 1; white-space: nowrap;
  }
  .card--back .brand { top: 100px; }
  .card--back .brand__mark { background: var(--paper); }
  .card--front .brand { top: 60px; color: var(--navy); }
  .card--front .brand__mark { background: var(--navy); }

  .pitch {
    position: absolute; top: 200px; left: 0; right: 0;
    text-align: center; font-size: 19px; line-height: 1.3; letter-spacing: 1px;
  }

  .identity {
    position: absolute; top: 145px; left: 0; right: 0; text-align: center;
  }
  .identity__rule {
    position: absolute; top: 42px; left: 0; right: 0; height: 2px; background: var(--rule);
  }
  .identity__company {
    position: relative; display: inline-block; background: var(--paper); padding: 0 18px;
    font-family: "Montserrat", sans-serif; font-weight: 600;
    font-size: 36px; letter-spacing: 1px; color: var(--navy);
  }
  .identity__title {
    display: block; margin-top: 4px; font-size: 20px; letter-spacing: 1.5px; color: var(--slate);
  }

  .contact {
    position: absolute; top: 265px; left: 0; right: 0;
    list-style: none; text-align: center;
    font-size: 21px; line-height: 1.4; letter-spacing: 2px; color: var(--ink);
  }
</style>
</head>
<body>
<main class="canvas">
  <section class="card card--back" aria-label="Card back">
    <div class="brand">
      <span class="brand__mark"></span>
      <span class="brand__name">KRV HOME SOLUTIONS</span>
    </div>
    <p class="pitch">
      Pay all cash. Buy in as is condition. No fees,Commisions<br>
      or closing costs.Close quick. No hassles with solutions<br>
      to meet your unique situation.<br>
      Call today for an offer within 24 hours.
    </p>
  </section>

  <section class="card card--front" aria-label="Card front">
    <div class="brand">
      <span class="brand__mark"></span>
      <span class="brand__name">KRV HOME SOLUTIONS</span>
    </div>
    <div class="identity">
      <span class="identity__rule"></span>
      <h1 class="identity__company">KRV HOME SOLUTIONS</h1>
      <span class="identity__title">Principal-Acquisitions</span>
    </div>
    <ul class="contact">
      <li>Phone : 555-214-0937</li>
      <li>Email : krvhomesolutions@fernmail.example</li>
      <li>Facebook : /krvhomesolutions</li>
      <li>Instagram:@krvhomesolutions</li>
    </ul>
  </section>
</main>
</body>
</html>
```